Larchvale Comfort Business Card Design

Design new, 2 sides, business cards for a residential and light commercial heating, air conditioning contractor.

Target Market(s)

Homeowners, small businesses

Industry/Entity Type

Business

Contact Information for Business Card

Dominic Westerhall
Phone - 862-415-2736
Email
Address - PO box 518
Brightwater NJ 07912
Website - www.HarborBreezeLLC.example

Requirements
Must have
• logo, company colors, standard size with no die cut, so I can use nova stamp

```html
<!DOCTYPE html>
<html lang="en">
<head>
<meta charset="utf-8">
<title>Larchvale Comfort Business Cards</title>
<link href="https://fonts.googleapis.com/css2?family=Open+Sans:wght@400;600;700&display=swap" rel="stylesheet">
<style>
  :root {
    --crimson: #9b1b3a;
    --orange: #f08a2c;
    --ink: #4a4a4a;
    --back-ink: #5a1a1f;
    --paper: #ffffff;
    --backdrop: #ece8e2;
  }
  * { margin: 0; padding: 0; box-sizing: border-box; }
  html, body {
    width: 1200px; height: 950px; overflow: hidden;
    background: var(--backdrop);
    font-family: "Open Sans", Arial, sans-serif;
  }
  .sheet {
    position: relative; width: 1200px; height: 950px;
    display: flex; justify-content: center; align-items: center; gap: 60px;
  }
  .card {
    position: relative; width: 420px; height: 735px; overflow: hidden;
    box-shadow: 0 6px 18px rgba(0,0,0,0.18);
  }
  /* front */
  .card-front { background: var(--crimson); }
  .card-front .frame { position: absolute; inset: 0; }
  .front-content {
    position: absolute; inset: 0;
    display: flex; flex-direction: column; align-items: center;
  }
  .brand-name {
    color: var(--crimson); font-weight: 700; font-size: 36px;
    line-height: 1; white-space: nowrap; text-align: center;
  }
  .front-content .brand-name { margin-top: 150px; }
  .person { margin-top: 112px; text-align: center; }
  .person-name {
    color: var(--crimson); font-weight: 600; font-size: 23px;
    text-transform: uppercase; letter-spacing: 0.5px;
  }
  .person-title { color: var(--orange); font-size: 16px; margin-top: 2px; }
  .contact { margin-top: 12px; color: var(--ink); font-size: 16px; line-height: 1.45; }
  .contact-line { display: flex; align-items: center; gap: 8px; white-space: nowrap; }
  .contact-line .icon { width: 15px; height: 15px; flex: none; }
  .contact-line.plain { padding-left: 23px; }
  /* back */
  .card-back {
    background: var(--orange);
    display: flex; flex-direction: column; align-items: center;
  }
  .card-back .brand-name { margin-top: 325px; font-size: 38px; }
  .tagline {
    position: absolute; bottom: 78px; left: 0; right: 0;
    text-align: center; color: var(--back-ink); font-size: 16px; line-height: 1.35;
  }
</style>
</head>
<body>
<main class="sheet">
  <section class="card card-front" aria-label="Card front">
    <svg class="frame" width="420" height="735" viewBox="0 0 420 735" aria-hidden="true">
      <path d="M0,52 Q210,18 420,52 L420,612 C335,612 262,630 232,668 L210,694 L188,668 C158,630 85,612 0,612 Z"
            fill="var(--paper)" stroke="var(--orange)" stroke-width="4"/>
    </svg>
    <div class="front-content">
      <div class="brand-name">Larchvale Comfort</div>
      <div class="person">
        <div class="person-name">Dominic Westerhall</div>
        <div class="person-title">CEO/Founder</div>
      </div>
      <div class="contact">
        <div class="contact-line plain">PO box 518</div>
        <div class="contact-line plain">Brightwater NJ 07912</div>
        <div class="contact-line">
          <svg class="icon" viewBox="0 0 16 16"><path d="M3 1h3l1.5 4-2 1.3a9 9 0 0 0 4.2 4.2L11 8.5l4 1.5v3c0 1-1 2-2 2A12 12 0 0 1 1 3c0-1 1-2 2-2z" fill="var(--crimson)"/></svg>
          862 415 2736
        </div>
        <div class="contact-line">
          <svg class="icon" viewBox="0 0 16 16"><rect x="4" y="1" width="8" height="5" fill="var(--crimson)"/><rect x="1" y="6" width="14" height="6" rx="1" fill="var(--crimson)"/><rect x="4" y="10" width="8" height="5" fill="#fff" stroke="var(--crimson)" stroke-width="1.5"/></svg>
          862 415 2737
        </div>
        <div class="contact-line">
          <svg class="icon" viewBox="0 0 16 16"><rect x="4" y="1" width="8" height="14" rx="1.5" fill="var(--crimson)"/><rect x="5.5" y="3" width="5" height="8" fill="#fff"/></svg>
          862 415 2738
        </div>
        <div class="contact-line">
          <svg class="icon" viewBox="0 0 16 16"><rect x="1" y="3" width="14" height="10" rx="1" fill="var(--crimson)"/><path d="M1.5 3.5 8 9l6.5-5.5" fill="none" stroke="#fff" stroke-width="1.3"/></svg>
          dominic@larchvalecomfort.example
        </div>
        <div class="contact-line">
          <svg class="icon" viewBox="0 0 16 16"><circle cx="8" cy="8" r="7" fill="var(--crimson)"/><path d="M1 8h14M8 1c-3 3-3 11 0 14M8 1c3 3 3 11 0 14" fill="none" stroke="#fff" stroke-width="1"/></svg>
          www.LarchvaleComfortLLC.example
        </div>
      </div>
    </div>
  </section>

  <section class="card card-back" aria-label="Card back">
    <div class="brand-name">Larchvale Comfort</div>
    <p class="tagline">Residential &amp; light commercial heating<br>Air conditioning contractor</p>
  </section>
</main>
</body>
</html>
```